TLV Accounting Firm Needs Graphic Art for Our Proven Processes and For Our Core Values

**Looking for redesign of attached Powerpoint content (see below)
***Final graphic should be good for web use

Date: March 10, 2017

From: Colin Ashdown, CPA
Ashdown, Pettifer & Associates, P.C. (TLV)

Background:

TLV is a 20 person Houston based CPA firm, providing tax, accounting, financial and consulting services, to individuals and to entrepreneurs and their businesses. TLV is engaged in a process called KLU (See the book Headway, by Lars Obermeyer) whereby we implement a “system” to operate our company. As part of this system we have defined what we call our “Proven Process”. This is something we will show all prospective clients, and have on our website, that explains what it looks like to work with us. Starting at the beginning of the project to completion.

Project Description:

TLV is looking for graphic artist assistance in designing the following pieces:

1. Graphic depiction of “The TLV Way”, otherwise known as our “Proven Process”. The first attachments labeled TLV will show what we have done ourselves. These will show the general steps we have defined in both a sort of graphic way and a step by step narrative. The second attachment shows you some actual examples other firms have put together, hopefully that will show you what we are asking you to develop for us. Note that we are very open to any suggested clarifications or improvements to what we have done which may include changing phrases or saying something in a different way. Remember we are accountants!

2. We have defined our core values as a company, and we are wanting to develop some posters/placards so we can post them in our conference rooms, break room, etc. Attached are our core values as well as some deeper narratives about what they mean. Also included are many of the “words” we kicked around before arriving at our core values.

3. You will also find an attachment with our logo that should be incorporated, as well. Designs SHOULD INCLUDE, but not be limited to, the colors on our logo. Our end product should reflect a strong sense of our core values.

We would like to have the project in a form that would give us the option to use any/all of the information on our website, posters, brochures, etc.

Thanks in advance for your assistance.

Target Market(s)

Entrepreneurs and their companies with revenue greater than one million; Industries such as real estate, construction, trades and professional services; all in the Greater Houston Texas area

Industry/Entity Type

Accounting

Font styles to use
Serif
Other font styles liked:
• We are okay with Serif but are open.

Requirements
Must have
• Proven Process must be presented in a way that is clear and makes sense.
Nice to have
• Clean lines
• Colors should go with logo (see attached)
Should not have
• Can't think of anything - unless I see it

```html
<!DOCTYPE html>
<html lang="en">
<head>
<meta charset="utf-8">
<title>TLV's Core Values</title>
<link rel="stylesheet" href="https://fonts.googleapis.com/css2?family=Archivo+Black&family=Roboto+Condensed:wght@300;400;700;900&family=Nunito:wght@800&family=Kaushan+Script&family=Arvo:wght@700&family=Cutive&display=swap">
<style>
  :root {
    --paper: #ffffff;
    --forest: #1f4a26;
    --lavender: #a9a5d6;
    --tan: #c2956a;
    --mint: #a9d9bd;
    --gold: #c9a22b;
    --sun: #f2d46f;
    --fog: #cfcfcf;
    --blush: #e9cbc5;
    --sage: #b4cda6;
    --slate: #8f90c0;
    --sky: #a8dbe7;
    --mist: #a9c0c6;
    --stone: #a9a9a9;
  }
  * { margin: 0; padding: 0; box-sizing: border-box; }
  html, body { width: 1200px; height: 900px; overflow: hidden; background: var(--paper); }
  .poster { position: relative; width: 1200px; height: 900px; background: var(--paper); }
  .poster-title {
    position: absolute; left: 61px; top: 78px;
    font-family: "Archivo Black", "Arial Black", sans-serif;
    font-size: 39px; letter-spacing: 0.6px; color: var(--forest);
  }
  .value {
    position: absolute; white-space: nowrap; line-height: 1;
    font-family: "Roboto Condensed", "Arial Narrow", sans-serif; font-weight: 400;
    transform: translate(-50%, -50%) rotate(var(--r, 0deg));
  }
  .value--core { font-weight: 900; color: var(--forest); font-size: 54px; letter-spacing: -0.5px; }
  .value--bold { font-weight: 700; }
  .value--light { font-weight: 300; }
  .value--round { font-family: "Nunito", "Arial Rounded MT Bold", sans-serif; font-weight: 800; }
  .value--script { font-family: "Kaushan Script", cursive; }
  .value--slab { font-family: "Arvo", "Rockwell", serif; font-weight: 700; }
  .value--type { font-family: "Cutive", "American Typewriter", serif; }

  .firm { position: absolute; left: 61px; top: 760px; font-family: "Roboto Condensed", "Arial Narrow", sans-serif; }
  .firm-name { display: flex; align-items: center; gap: 10px; font-size: 26px; font-weight: 700; color: var(--forest); }
  .firm-square { width: 14px; height: 14px; background: var(--gold); }
  .firm-tagline { margin-top: 8px; margin-left: 24px; font-size: 18px; font-weight: 400; color: var(--gold); letter-spacing: 1px; }
</style>
</head>
<body>
<main class="poster">
  <h1 class="poster-title">TLV’S CORE VALUES</h1>

  <div class="value-cloud">
    <span class="value" style="left:106px;top:330px;--r:70deg;font-size:29px;color:var(--lavender)">Motivated</span>
    <span class="value" style="left:218px;top:302px;--r:-40deg;font-size:29px;color:var(--tan)">Gets it done</span>
    <span class="value value--round" style="left:296px;top:296px;--r:-40deg;font-size:30px;color:var(--mint)">Hungry for achievement</span>
    <span class="value" style="left:394px;top:296px;--r:20deg;font-size:30px;color:var(--gold)">humor</span>
    <span class="value value--type" style="left:442px;top:282px;--r:60deg;font-size:20px;color:var(--slate)">Positive</span>
    <span class="value" style="left:504px;top:274px;--r:25deg;font-size:29px;color:var(--sun)">Fair</span>
    <span class="value value--bold" style="left:589px;top:246px;font-size:31px;color:var(--fog)">Happy</span>
    <span class="value" style="left:718px;top:278px;--r:10deg;font-size:29px;color:var(--mint)">Encourager</span>
    <span class="value" style="left:792px;top:246px;--r:5deg;font-size:28px;color:var(--blush)">Honest always</span>
    <span class="value value--round" style="left:906px;top:270px;--r:-25deg;font-size:26px;color:var(--sage)">Energetic</span>
    <span class="value" style="left:1044px;top:286px;--r:-40deg;font-size:28px;color:var(--slate)">Creative</span>
    <span class="value value--core" style="left:1098px;top:334px;--r:55deg;font-size:57px">Fun</span>

    <span class="value" style="left:382px;top:368px;--r:40deg;font-size:21px;color:var(--slate)">growth minded</span>
    <span class="value value--script" style="left:538px;top:342px;--r:-35deg;font-size:30px;color:var(--sun)">Great Attitude</span>
    <span class="value value--core" style="left:548px;top:400px;--r:-38deg">Value Long Term</span>
    <span class="value value--core" style="left:600px;top:430px;--r:-40deg">Relationships</span>
    <span class="value" style="left:836px;top:336px;--r:8deg;font-size:29px;color:var(--slate)">Respectful</span>
    <span class="value" style="left:952px;top:356px;--r:68deg;font-size:30px;color:var(--sun)">Competitive</span>
    <span class="value" style="left:1054px;top:382px;--r:15deg;font-size:30px;color:var(--lavender)">Empathetic</span>

    <span class="value value--slab" style="left:272px;top:396px;--r:-12deg;font-size:29px;color:var(--lavender)">Servant</span>
    <span class="value" style="left:370px;top:430px;--r:12deg;font-size:28px;color:var(--gold)">Listens</span>
    <span class="value" style="left:816px;top:380px;--r:-30deg;font-size:29px;color:var(--sun)">Trust</span>
    <span class="value" style="left:864px;top:402px;--r:-20deg;font-size:32px;color:var(--fog)">Clients</span>
    <span class="value" style="left:738px;top:420px;--r:-75deg;font-size:26px;color:var(--sky)">Professional</span>

    <span class="value value--core" style="left:180px;top:491px;--r:35deg">Team Player</span>
    <span class="value value--bold" style="left:250px;top:462px;font-size:26px;color:var(--gold)">excellence</span>
    <span class="value value--light" style="left:684px;top:480px;--r:85deg;font-size:34px;color:var(--fog)">Integrity</span>
    <span class="value" style="left:822px;top:468px;--r:12deg;font-size:29px;color:var(--sky)">Tenacious</span>
    <span class="value value--core" style="left:1016px;top:544px;--r:55deg">Conscientious</span>
    <span class="value value--type" style="left:1056px;top:478px;--r:38deg;font-size:22px;color:var(--gold)">Committed</span>

    <span class="value" style="left:324px;top:512px;--r:-35deg;font-size:29px;color:var(--mint)">Ethical</span>
    <span class="value" style="left:150px;top:558px;--r:30deg;font-size:27px;color:var(--stone)">Accountable</span>
    <span class="value" style="left:436px;top:576px;--r:30deg;font-size:27px;color:var(--stone)">always learning</span>
    <span class="value" style="left:540px;top:552px;--r:-30deg;font-size:27px;color:var(--slate)">Smiles</span>
    <span class="value value--bold" style="left:626px;top:550px;font-size:26px;color:var(--stone)">minded</span>
    <span class="value value--script" style="left:792px;top:548px;--r:-15deg;font-size:30px;color:var(--gold)">Works well with others</span>
    <span class="value" style="left:912px;top:570px;--r:-60deg;font-size:31px;color:var(--mist)">Helpful</span>

    <span class="value value--round" style="left:294px;top:618px;--r:-15deg;font-size:23px;color:var(--sage)">Deliver Value</span>
    <span class="value" style="left:408px;top:634px;--r:-30deg;font-size:27px;color:var(--sky)">Well</span>
    <span class="value value--script" style="left:544px;top:636px;--r:-35deg;font-size:25px;color:var(--sun)">Winner</span>
    <span class="value value--core" style="left:764px;top:630px;--r:-20deg">Caring</span>
    <span class="value" style="left:964px;top:622px;--r:-15deg;font-size:27px;color:var(--gold)">Strives</span>
  </div>

  <footer class="firm">
    <p class="firm-name"><span class="firm-square"></span>Ashdown, Pettifer &amp; Associates, PC</p>
    <p class="firm-tagline">CPAs &amp; Advisors</p>
  </footer>
</main>
</body>
</html>
```